TK Stationery - Modern Contemporary

Develop modern template for Letterhead and Stationery (business card, letterhead, envelopes) using the TK Logo and Icon

Colors
0054AA
0677BA
7BADD7
CADEEF
E8F1F8
00AB8E
00BBA5
67D7C9
C6EFE9
E9F9F6
EE7325
F08F49
F5BC92
FAE3D3
FDF4ED
6B429C
8869AF
B7A5CE
E3DAEB
F3F0F8

```html
<!DOCTYPE html>
<html lang="en">
<head>
<meta charset="utf-8">
<title>TK Studio Letterhead</title>
<link href="https://fonts.googleapis.com/css2?family=Open+Sans:wght@400;600&family=PT+Sans:wght@400&display=swap" rel="stylesheet">
<style>
  :root {
    --backdrop: #e9e9e9;
    --paper: #ffffff;
    --navy: #262b49;
    --green: #2fb56c;
    --orange: #ee7325;
    --text: #4a4a4a;
    --text-soft: #555555;
  }
  * { box-sizing: border-box; margin: 0; padding: 0; }
  html, body {
    width: 1154px; height: 1200px; overflow: hidden;
    background: var(--backdrop);
  }
  .letterhead {
    position: absolute; left: 187px; top: 53px;
    width: 780px; height: 1093px;
    background: var(--paper);
    font-family: "PT Sans", Arial, sans-serif;
    color: var(--text);
  }
  .brand-name {
    position: absolute; left: 60px; top: 44px;
    font-family: "PT Sans", Arial, sans-serif;
    font-size: 38px; font-weight: 400; letter-spacing: 0.5px;
    color: var(--navy);
  }
  .contact {
    position: absolute; right: 60px; top: 53px;
    text-align: right;
    font-family: "Open Sans", Arial, sans-serif;
    font-size: 12.5px; line-height: 17px; color: var(--text-soft);
  }
  .contact .address { margin-bottom: 5px; }
  .contact .line { display: flex; justify-content: flex-end; align-items: center; gap: 5px; }
  .contact svg { width: 11px; height: 11px; }
  .recipient { position: absolute; left: 60px; top: 290px; }
  .recipient .name {
    font-size: 15px; color: #505050; text-transform: uppercase; margin-bottom: 4px;
  }
  .recipient .meta { font-size: 11.5px; line-height: 19px; color: #505050; }
  .body-copy { position: absolute; left: 60px; top: 386px; width: 660px; }
  .body-copy p {
    font-size: 11.5px; line-height: 19px; text-align: justify;
    color: var(--text); margin-bottom: 17px;
  }
  .closing { position: absolute; left: 60px; top: 690px; font-size: 13px; color: #505050; }
  .signature {
    position: absolute; left: 60px; top: 712px; width: 158px; height: 38px;
    background: linear-gradient(90deg, #e6e8f0, #f1f2f6);
    border-radius: 3px;
  }
  .footer-band { position: absolute; left: 0; bottom: 0; width: 780px; height: 35px; }
  .footer-band .web {
    position: absolute; right: 23px; top: 8px;
    font-family: "Open Sans", Arial, sans-serif; font-weight: 600;
    font-size: 14.5px; color: #ffffff;
  }
</style>
</head>
<body>
  <main class="letterhead">
    <div class="brand-name">tk studio</div>

    <div class="contact">
      <div class="address">418 Harbor Crest Way<br>Bayview CA 90210</div>
      <div class="line">555-014-2270
        <svg viewBox="0 0 12 12" aria-hidden="true"><path d="M3 1l2 2.5-1.2 1.2c.6 1.4 1.8 2.6 3.2 3.2L8.2 6.7 10.8 8.6 9.8 10.8C5 10.5 1.5 7 1.2 2.2z" fill="var(--green)"/></svg>
      </div>
      <div class="line">dholt@tkstudio.com
        <svg viewBox="0 0 12 12" aria-hidden="true"><rect x="1" y="3" width="10" height="7" fill="var(--orange)"/><path d="M1 3l5 4 5-4" stroke="#fff" stroke-width="1" fill="none"/></svg>
      </div>
    </div>

    <section class="recipient">
      <div class="name">Darren Holt</div>
      <div class="meta">President / CEO<br>City/State, Zip Code</div>
    </section>

    <section class="body-copy">
      <p>Lorem Ipsum is simply dummy text of the printing and typesetting industry. Lorem Ipsum has been the industry's standard dummy text ever since the 1500s, when an unknown printer took a galley of type and scrambled it to make a type specimen book. It has survived not only five centuries, but also the leap into electronic typesetting, remaining essentially unchanged. It was popularised in the 1960s with the release of Letraset sheets containing Lorem Ipsum passages, and more recently with desktop publishing software like Aldus PageMaker including versions of Lorem Ipsum.</p>
      <p>It is a long established fact that a reader will be distracted by the readable content of a page when looking at its layout. The point of using Lorem Ipsum is that it has a more-or-less normal distribution of letters, as opposed to using 'Content here, content here', making it look like readable English. Many desktop publishing packages and web page editors now use Lorem Ipsum as their default model text, and a searchaccident, sometimes on purpose (injected humour and the like).</p>
      <p>There are many variations of passages of Lorem Ipsum available, but the majority have suffered alteration in some form, by injected humour, or randomised words which don't look even slightly believable. If you are going to use a passage of Lorem Ipsum, you need to be sure there isn't anything embarrassing hidden in the middle of text.</p>
    </section>

    <div class="closing">Sincerely,</div>
    <div class="signature" role="img" aria-label="Handwritten signature of the sender"></div>

    <div class="footer-band">
      <svg width="780" height="35" viewBox="0 0 780 35" aria-hidden="true">
        <polygon points="0,7 562,7 555,13 0,13" fill="var(--green)"/>
        <polygon points="0,19 555,19 578,0 780,0 780,35 0,35" fill="var(--navy)"/>
      </svg>
      <span class="web">www.tkstudio.com</span>
    </div>
  </main>
</body>
</html>
```